Health and wellnes company needs business cards

We are a Health and wellness business just relocated to Spain. Here nobody knows our business so we would like to put some of our services on the card. Clean design with logo.

Contact Information for Business Card

Brightmeadow
Paula & Oskar Dunbeck
Calle del Almendro 57
Villarrosa del Mar
Mobile: 0046 731 402687
info@brightmeadow.example

Font styles to use
Serif

Colors
85cae6
85acd3
b768aa

Requirements
Must have
• these Services somewhere on the card
• - Private or group yoga
• - Reconnective healing
• - Kitesurfing lessons
• - Massage
• LOgo somewhere
Nice to have
• Colours that go with the logo please

```html
<!DOCTYPE html>
<html lang="en">
<head>
<meta charset="utf-8">
<title>Brightmeadow business card</title>
<link rel="stylesheet" href="https://fonts.googleapis.com/css2?family=Marcellus&family=Roboto:wght@400;500;700&display=swap">
<style>
  :root {
    --navy: #1c3661;
    --teal: #6cc5c7;
    --paper: #f7f8fb;
    --ink: #474a52;
    --backdrop: #b4b4b4;
    --white: #f2f2f4;
  }
  * { margin: 0; padding: 0; box-sizing: border-box; }
  html, body { width: 1172px; height: 1200px; overflow: hidden; }
  body {
    background: var(--backdrop);
    font-family: "Roboto", Arial, sans-serif;
    position: relative;
  }
  .card {
    position: absolute;
    left: 214px;
    width: 744px;
    height: 425px;
  }
  .card-front { top: 122px; background: var(--navy); }
  .card-back { top: 645px; height: 430px; background: var(--paper); }

  .brand-ring {
    position: absolute;
    border-radius: 50%;
    border: 9px solid var(--teal);
  }
  .card-front .brand-ring { left: 297px; top: 102px; width: 148px; height: 148px; }
  .card-back .brand-ring { left: 93px; top: 50px; width: 106px; height: 106px; border-width: 7px; }

  .brand-name {
    position: absolute;
    font-family: "Marcellus", Georgia, serif;
    font-weight: 400;
    white-space: nowrap;
    line-height: 1;
  }
  .card-front .brand-name {
    left: 0; width: 100%; text-align: center;
    top: 264px; font-size: 42px; color: var(--white);
  }
  .card-back .brand-name {
    left: 25px; top: 164px; font-size: 29px; color: var(--navy);
  }
  .website {
    position: absolute; left: 0; width: 100%; text-align: center;
    top: 360px; font-size: 22px; letter-spacing: 2.5px; color: var(--teal);
  }
  .website .domain { color: var(--white); }

  .holder {
    position: absolute; right: 27px; top: 46px; text-align: right;
  }
  .holder-name { font-size: 29px; font-weight: 700; color: var(--navy); line-height: 1.2; }
  .holder-role { font-size: 22px; color: var(--teal); line-height: 1.2; }
  .holder-tab {
    position: absolute; right: 0; top: 49px; width: 11px; height: 53px; background: var(--navy);
  }

  .address, .contact {
    position: absolute; left: 25px; font-size: 21.5px; color: var(--ink); line-height: 28px;
  }
  .address { top: 260px; font-style: normal; }
  .contact { top: 340px; }
  .contact li { list-style: none; display: flex; align-items: center; gap: 10px; }
  .contact svg { width: 16px; height: 16px; fill: var(--navy); }

  .services {
    position: absolute; right: 28px; top: 242px; text-align: right;
  }
  .services h2 { font-size: 23px; font-weight: 700; color: var(--navy); margin-bottom: 4px; }
  .services li {
    list-style: none; font-size: 21.5px; color: var(--ink); line-height: 28.5px;
    display: flex; justify-content: flex-end; align-items: center; gap: 10px;
  }
  .services li::after {
    content: ""; width: 10px; height: 10px; border-radius: 50%; background: var(--navy);
  }
  .band { position: absolute; bottom: 0; height: 18px; width: 50%; }
  .band-navy { left: 0; background: var(--navy); }
  .band-teal { right: 0; background: var(--teal); }
</style>
</head>
<body>
  <section class="card card-front">
    <div class="brand-ring"></div>
    <div class="brand-name">BRIGHTMEADOW</div>
    <div class="website">www.<span class="domain">brightmeadow</span>.example</div>
  </section>

  <section class="card card-back">
    <div class="brand-ring"></div>
    <div class="brand-name">BRIGHTMEADOW</div>

    <div class="holder">
      <div class="holder-name">Paula &amp; Oskar Dunbeck</div>
      <div class="holder-role">Co-Founder</div>
    </div>
    <div class="holder-tab"></div>

    <address class="address">
      Calle del Almendro 57<br>Villarrosa del Mar
    </address>

    <ul class="contact">
      <li>
        <svg viewBox="0 0 16 16" aria-hidden="true"><path d="M3.6 1.2l2.2 2.6-1.3 1.8c.8 2 2.3 3.6 4.3 4.6l1.8-1.3 2.6 2.2-1.5 2.6C6.6 13.5 2.4 9.2 1.1 3.1z"/></svg>
        0046 731 402687
      </li>
      <li>
        <svg viewBox="0 0 16 16" aria-hidden="true"><path d="M1 3h14v10H1z M2.5 4.5v.4L8 9l5.5-4.1v-.4z" fill-rule="evenodd"/></svg>
        info@brightmeadow.example
      </li>
    </ul>

    <div class="services">
      <h2>Services</h2>
      <ul>
        <li>Private or group yoga</li>
        <li>Reconnective healing</li>
        <li>Kitesurfing lessons</li>
        <li>Massage</li>
      </ul>
    </div>

    <div class="band band-navy"></div>
    <div class="band band-teal"></div>
  </section>
</body>
</html>
```